Simple and Clean business card design

We would like the design to be simple clean and to incorporate our colors.

We are open to your design and talent, we have the dots in our logo as we think of it as data points and we connect data points for people.

We are open to see the great creative and clean design you bring to the table

Contact Information for Business Card

please include: name, position, email, phone and website

Font styles to use
Sans Serif

Requirements
Must have
• my colors incorporated, simplicity
Nice to have
• lots of white space, simplicity
Should not have
• complexicity/ complex art

```html
<!DOCTYPE html>
<html lang="en">
<head>
<meta charset="utf-8">
<title>Nectra Business Card</title>
<link rel="stylesheet" href="https://fonts.googleapis.com/css2?family=Montserrat:wght@700&family=Work+Sans:wght@400;500;600&display=swap">
<style>
  :root {
    --backdrop: #1e1e1f;
    --card-dark: #000000;
    --card-light: #ffffff;
    --ink: #111111;
    --brand-blue: #4f7fc8;
    --brand-green: #2ea04a;
    --brand-yellow: #f4b41a;
    --brand-red: #e43d30;
    --divider: #8fa9d6;
  }
  * { box-sizing: border-box; margin: 0; padding: 0; }
  html, body {
    width: 1200px; height: 852px; overflow: hidden;
    background: var(--backdrop);
  }
  .stage {
    width: 1200px; height: 852px;
    display: flex; flex-direction: column; align-items: center; justify-content: center;
    gap: 36px;
  }
  .card {
    position: relative;
    width: 650px; height: 371px;
    border-radius: 18px;
    overflow: hidden;
    box-shadow: 0 18px 40px rgba(0,0,0,.55);
  }
  .card--front { background: var(--card-dark); }
  .card--back { background: var(--card-light); }

  .color-band {
    position: absolute; left: 0; right: 0; bottom: 0; height: 9px;
    display: flex;
  }
  .color-band span { flex: 1; }
  .color-band .blue { background: var(--brand-blue); }
  .color-band .green { background: var(--brand-green); }
  .color-band .yellow { background: var(--brand-yellow); }
  .color-band .red { background: var(--brand-red); }

  .wordmark {
    font-family: "Montserrat", sans-serif;
    font-weight: 700;
    letter-spacing: -1px;
    line-height: 1;
    display: flex; align-items: center; gap: 14px;
  }
  .wordmark__dot {
    width: 16px; height: 16px; border-radius: 50%;
    background: var(--brand-blue);
  }
  .card--front .wordmark {
    position: absolute; left: 50%; top: 50%;
    transform: translate(-50%, -55%);
    font-size: 96px; color: #ffffff;
  }
  .card--back .wordmark {
    position: absolute; left: 44px; bottom: 86px;
    font-size: 74px; color: var(--ink);
  }

  .divider {
    position: absolute; left: 358px; top: 70px;
    width: 1px; height: 150px; background: var(--divider);
  }
  .contact {
    position: absolute; left: 380px; top: 66px;
    font-family: "Work Sans", sans-serif; color: var(--ink);
  }
  .contact__name {
    font-family: "Montserrat", sans-serif; font-weight: 700;
    font-size: 21px; letter-spacing: 1.5px; color: var(--brand-blue);
    text-transform: uppercase;
  }
  .contact__role { font-size: 15px; margin-top: 2px; }
  .contact__address { font-size: 15px; line-height: 1.3; margin-top: 12px; }
  .contact__list { list-style: none; margin-top: 10px; font-size: 15px; line-height: 1.35; }
  .contact__list li { display: flex; align-items: center; gap: 7px; }
  .contact__list svg { width: 11px; height: 11px; flex: none; }
</style>
</head>
<body>
<main class="stage">
  <section class="card card--front" aria-label="Card front">
    <div class="wordmark"><span class="wordmark__dot"></span>Nectra</div>
    <div class="color-band"><span class="blue"></span><span class="green"></span><span class="yellow"></span><span class="red"></span></div>
  </section>

  <section class="card card--back" aria-label="Card back">
    <div class="wordmark"><span class="wordmark__dot"></span>Nectra</div>
    <div class="divider"></div>
    <div class="contact">
      <p class="contact__name">Daniel Reyes</p>
      <p class="contact__role">Founder</p>
      <p class="contact__address">418 Brookfield Lane<br>Marlow, TX 75002</p>
      <ul class="contact__list">
        <li>
          <svg viewBox="0 0 12 12" aria-hidden="true"><path d="M2.5 1h2l1 3-1.3 1a6.5 6.5 0 0 0 2.8 2.8l1-1.3 3 1v2a1 1 0 0 1-1 1A9.5 9.5 0 0 1 1.5 2a1 1 0 0 1 1-1z" fill="var(--brand-blue)"/></svg>
          0412 880 317
        </li>
        <li>
          <svg viewBox="0 0 12 12" aria-hidden="true"><rect x="1" y="2.5" width="10" height="7" fill="none" stroke="var(--brand-blue)" stroke-width="1.2"/><path d="M1 3l5 3.5L11 3" fill="none" stroke="var(--brand-blue)" stroke-width="1.2"/></svg>
          info@nectradata.com
        </li>
        <li>
          <svg viewBox="0 0 12 12" aria-hidden="true"><circle cx="6" cy="6" r="5" fill="none" stroke="var(--brand-blue)" stroke-width="1.1"/><ellipse cx="6" cy="6" rx="2.2" ry="5" fill="none" stroke="var(--brand-blue)" stroke-width="1"/><path d="M1 6h10" stroke="var(--brand-blue)" stroke-width="1"/></svg>
          www.nectradata.com
        </li>
      </ul>
    </div>
    <div class="color-band"><span class="blue"></span><span class="green"></span><span class="yellow"></span><span class="red"></span></div>
  </section>
</main>
</body>
</html>
```